A business card design for a dental office. We have Two doctors working here. We practice general de

I already have a logo designed for the office with the name and a slogan.
Now I need to create design for a business card using the same logo.
Details Needed on the front side of the card are :
Bernard K. Oswin, DDS
Gerald M Fenwick, DDS
418 Birch Lane
Kellfield, VT 00000
Phone : 555 019 4831
Fax : 555 019 4832
Website : WWW.BrightmoorToothHaven.Com
Office hours by appointment
On the back side of the card need :
Appointment
Date....................Time...................
With....................................
If unable to keep your appointment, please give 24-48 hours notice in order to avoid broken appointment fee.

Industry/Entity Type

Dental Clinic

Contact Information for Business Card

Bernard K. Oswin, DDS
Gerald M Fenwick, DDS
418 Birch Lane
Kellfield, VT 00000
Phone : 555 019 4831
Fax : 555 019 4832
Appointment

Requirements
Must have
• Keep the Name and slogan on the logo on the front of the card. You can move them around the Logo and Name/Slogan of business (Oswin Family Dentistry/Gentle care for every grin) as you wish to get a feel of the design.
• Bernard K. Oswin, DDS
• Gerald M Fenwick, DDS
• 418 Birch Lane
• Kellfield, VT 00000
• Phone : 555 019 4831
• Fax : 555 019 4832
• WWW.BrightmoorToothHaven.Com
• Keep these three groups above as they are together now in different areas of the front side.
• On the back side of the card need :
• Appointment
• Date....................Time...................
• With....................................
• If unable to keep your appointment, please give 24-48 hours notice in order to avoid broken appointment fee.

```html
<!DOCTYPE html>
<html lang="en">
<head>
<meta charset="utf-8">
<title>Oswin Family Dentistry – Business Card</title>
<link rel="stylesheet" href="https://fonts.googleapis.com/css2?family=Source+Sans+3:ital,wght@0,400;0,600;1,400;1,600&display=swap">
<style>
  :root {
    --backdrop: #a4a4a4;
    --card: #f4f4f5;
    --brand-blue: #1d5ca8;
    --band-blue: #1b5aa5;
    --accent-red: #d2373c;
    --text-grey: #555a60;
    --dots: #7d7f83;
    --divider: #b9bcc1;
  }
  * { box-sizing: border-box; margin: 0; padding: 0; }
  html, body { width: 1105px; height: 1200px; overflow: hidden; }
  body {
    background: var(--backdrop);
    font-family: "Source Sans 3", "Myriad Pro", sans-serif;
    position: relative;
  }
  .card {
    position: absolute;
    left: 182px;
    width: 747px;
    height: 427px;
    background: var(--card);
    overflow: hidden;
  }
  .card--front { top: 119px; }
  .card--back { top: 635px; }

  /* Front */
  .brand-mark {
    position: absolute; left: 160px; top: 78px;
    width: 98px; height: 98px; border-radius: 50%;
    background: var(--brand-blue);
  }
  .brand-name {
    position: absolute; left: 278px; top: 110px;
    font-size: 23px; font-weight: 600; letter-spacing: 1.6px;
    color: var(--brand-blue); text-transform: uppercase; white-space: nowrap;
  }
  .brand-slogan {
    position: absolute; left: 280px; top: 145px; width: 330px;
    display: flex; align-items: center; gap: 8px;
    font-size: 10.5px; letter-spacing: 1.2px; color: var(--accent-red);
    text-transform: uppercase; white-space: nowrap;
  }
  .brand-slogan::before, .brand-slogan::after {
    content: ""; flex: 1; height: 1px; background: var(--divider);
  }
  .doctors {
    position: absolute; right: 349px; top: 220px; text-align: right;
    color: var(--brand-blue); font-size: 27px; line-height: 31px; font-weight: 400;
    white-space: nowrap;
  }
  .doctors .degree { font-size: 19px; }
  .address {
    position: absolute; right: 349px; top: 289px;
    font-size: 19.5px; color: var(--text-grey); white-space: nowrap;
  }
  .divider {
    position: absolute; left: 420px; top: 224px; width: 1px; height: 92px;
    background: var(--divider);
  }
  .contacts { position: absolute; left: 444px; top: 222px; list-style: none; }
  .contacts li {
    display: flex; align-items: center; gap: 9px;
    height: 31.5px; font-size: 19.5px; color: var(--text-grey); white-space: nowrap;
  }
  .contacts svg { width: 18px; height: 18px; fill: var(--brand-blue); flex: none; }
  .rule-red {
    position: absolute; left: 0; right: 0; top: 380px; height: 2px; background: var(--accent-red);
  }
  .hours-band {
    position: absolute; left: 0; right: 0; top: 387px; height: 40px;
    background: var(--band-blue); color: #fff;
    display: flex; align-items: center; justify-content: center;
    font-size: 20px; font-style: italic; font-weight: 600;
  }

  /* Back */
  .appt-title {
    position: absolute; left: 39px; top: 33px;
    font-size: 28px; font-weight: 600; color: var(--brand-blue);
  }
  .field {
    position: absolute; display: flex; align-items: flex-end; gap: 10px;
    font-size: 20px; color: var(--brand-blue); white-space: nowrap;
  }
  .field .line { flex: 1; border-bottom: 2px dotted var(--dots); margin-bottom: 5px; }
  .field .unit { font-size: 15px; margin-bottom: 2px; }
  .field--name { left: 39px; top: 102px; width: 646px; }
  .field--date { left: 36px; top: 170px; width: 358px; }
  .field--time { left: 414px; top: 170px; width: 274px; }
  .field--note { left: 39px; top: 232px; width: 646px; }
  .note-line {
    position: absolute; left: 39px; width: 646px; border-bottom: 2px dotted var(--dots);
  }
  .note-line--1 { top: 293px; }
  .note-line--2 { top: 334px; }
  .cancel-notice {
    position: absolute; left: 0; right: 0; top: 355px; text-align: center;
    font-size: 15.5px; line-height: 21px; font-style: italic; color: var(--text-grey);
  }
</style>
</head>
<body>
  <section class="card card--front" aria-label="Business card front">
    <div class="brand-mark" aria-hidden="true"></div>
    <div class="brand-name">Oswin Family Dentistry</div>
    <div class="brand-slogan">Gentle care for every grin</div>

    <div class="doctors">
      <div>Bernard K. Oswin, <span class="degree">DDS</span></div>
      <div>Gerald M Fenwick, <span class="degree">DDS</span></div>
    </div>
    <div class="address">418 Birch Lane, Kellfield, VT 00000</div>

    <div class="divider"></div>

    <ul class="contacts">
      <li>
        <svg viewBox="0 0 24 24" aria-label="Phone"><path d="M6.6 10.8a15 15 0 0 0 6.6 6.6l2.2-2.2a1 1 0 0 1 1-.25 11.4 11.4 0 0 0 3.6.6 1 1 0 0 1 1 1V20a1 1 0 0 1-1 1A17 17 0 0 1 3 4a1 1 0 0 1 1-1h3.5a1 1 0 0 1 1 1c0 1.25.2 2.45.6 3.6a1 1 0 0 1-.25 1z"/></svg>
        555 019 4831
      </li>
      <li>
        <svg viewBox="0 0 24 24" aria-label="Fax"><path d="M6 2h10l2 2v5H6z"/><path d="M2 10h20v9H18v-3H6v3H2z"/><path d="M7 17h10v5H7z"/></svg>
        555 019 4832
      </li>
      <li>
        <svg viewBox="0 0 24 24" aria-label="Website"><path d="M12 2a10 10 0 1 0 0 20 10 10 0 0 0 0-20zm-1 17.9A8 8 0 0 1 4.2 9.2L9 14v1a2 2 0 0 0 2 2zm6.9-2.5A2 2 0 0 0 16 16h-1v-3a1 1 0 0 0-1-1H8v-2h2a1 1 0 0 0 1-1V7h2a2 2 0 0 0 2-2v-.4a8 8 0 0 1 2.9 12.8z"/></svg>
        BrightmoorToothHaven.Com
      </li>
    </ul>

    <div class="rule-red"></div>
    <div class="hours-band">Office hours by appointment</div>
  </section>

  <section class="card card--back" aria-label="Business card back">
    <h2 class="appt-title">Next Appointment</h2>
    <div class="field field--name">Name :<span class="line"></span></div>
    <div class="field field--date">Date :<span class="line"></span></div>
    <div class="field field--time">Time :<span class="line"></span><span class="unit">AM/PM</span></div>
    <div class="field field--note">Note :<span class="line"></span></div>
    <div class="note-line note-line--1"></div>
    <div class="note-line note-line--2"></div>
    <p class="cancel-notice">Please give me 24 hours notice if you are unable to keep your appointment or<br>a cancellation fee may be charged.</p>
  </section>
</body>
</html>
```